BRISKEL Need a luxury modern business card designed.

Need a luxury modern business card designed. refer to the uploaded files for the company name and logo in the zip file under source files. i will making my descion on monday. so please send in before then so if we need to edit we will have the time. we have a trade show coming up and im on a deadline for printer.

Target Market(s)

high end clients

Contact Information for Business Card

Company nAme and logo. Tobias Fennick Co-Founder / Project Manager Office # 555-318-7094 Cell # 555-642-1586 BRISKEL.CA Tobias@briskel-example.ca

Font styles to use
Other font styles liked:
• Modern

Requirements
Must have
• Company name and logo, contact info, using the black, gold and white color scheme.

```html
<!DOCTYPE html>
<html lang="en">
<head>
<meta charset="utf-8">
<title>BRISKEL Business Card</title>
<link rel="stylesheet" href="https://fonts.googleapis.com/css2?family=Montserrat:wght@300;400;500;600&family=Nunito:wght@400;600&display=swap">
<style>
  :root {
    --page: #161616;
    --card: #333333;
    --gold: #a89a6a;
    --white: #f4f4f2;
    --muted: #d8d8d4;
  }
  html, body {
    margin: 0;
    padding: 0;
    width: 1200px;
    height: 900px;
    overflow: hidden;
    background: var(--page);
  }
  .canvas {
    width: 1200px;
    height: 900px;
    display: flex;
    flex-direction: column;
    align-items: center;
    justify-content: center;
    gap: 34px;
  }
  .card {
    position: relative;
    width: 700px;
    height: 400px;
    background: var(--card);
    box-sizing: border-box;
    border-left: 4px solid var(--gold);
    border-bottom: 4px solid var(--gold);
    box-shadow: 0 18px 40px rgba(0,0,0,.55);
  }
  .wordmark {
    display: flex;
    flex-direction: column;
    align-items: stretch;
  }
  .wordmark-name {
    font-family: "Montserrat", sans-serif;
    font-weight: 300;
    color: var(--white);
    letter-spacing: .18em;
    line-height: 1;
    display: flex;
    align-items: center;
    gap: .45em;
  }
  .wordmark-square {
    width: .38em;
    height: .38em;
    background: var(--gold);
  }
  .wordmark-tag {
    font-family: "Montserrat", sans-serif;
    font-weight: 500;
    color: var(--white);
    display: flex;
    align-items: center;
    gap: 10px;
    margin-top: 8px;
    white-space: nowrap;
  }
  .wordmark-tag::before,
  .wordmark-tag::after {
    content: "";
    flex: 1;
    height: 1px;
    background: var(--white);
  }

  /* front */
  .card-front .wordmark {
    position: absolute;
    right: 48px;
    top: 70px;
  }
  .card-front .wordmark-name { font-size: 50px; }
  .card-front .wordmark-tag { font-size: 11px; letter-spacing: .42em; }

  /* back */
  .card-back .wordmark {
    position: absolute;
    left: 50%;
    top: 62px;
    transform: translateX(-50%);
  }
  .card-back .wordmark-name { font-size: 38px; }
  .card-back .wordmark-tag { font-size: 8.5px; letter-spacing: .4em; }
  .rule {
    position: absolute;
    left: 70px;
    right: 70px;
    top: 178px;
    height: 1px;
    background: var(--gold);
  }
  .person {
    position: absolute;
    left: 70px;
    top: 236px;
    text-align: right;
    width: 280px;
  }
  .person-name {
    font-family: "Montserrat", sans-serif;
    font-weight: 500;
    font-size: 24px;
    color: var(--gold);
    margin: 0;
    letter-spacing: .02em;
  }
  .person-role {
    font-family: "Nunito", sans-serif;
    font-size: 17px;
    color: var(--white);
    margin: 4px 0 0;
  }
  .divider {
    position: absolute;
    left: 378px;
    top: 214px;
    width: 1px;
    height: 110px;
    background: var(--gold);
  }
  .contact {
    position: absolute;
    left: 410px;
    top: 222px;
    list-style: none;
    margin: 0;
    padding: 0;
    font-family: "Nunito", sans-serif;
    font-size: 18px;
    color: var(--white);
  }
  .contact li {
    display: flex;
    align-items: center;
    gap: 12px;
    height: 25px;
  }
  .contact svg {
    width: 16px;
    height: 16px;
    flex: none;
  }
  .contact .accent { color: var(--gold); }
</style>
</head>
<body>
<main class="canvas">
  <section class="card card-front" aria-label="Card front">
    <div class="wordmark">
      <div class="wordmark-name"><span class="wordmark-square"></span>BRISKEL</div>
      <div class="wordmark-tag">LUXURY LANDSCAPES</div>
    </div>
  </section>

  <section class="card card-back" aria-label="Card back">
    <div class="wordmark">
      <div class="wordmark-name"><span class="wordmark-square"></span>BRISKEL</div>
      <div class="wordmark-tag">LUXURY LANDSCAPES</div>
    </div>
    <div class="rule"></div>
    <div class="person">
      <h1 class="person-name">TOBIAS FENNICK</h1>
      <p class="person-role">Co-Founder | Project Manager</p>
    </div>
    <div class="divider"></div>
    <ul class="contact">
      <li>
        <svg viewBox="0 0 16 16" fill="none" stroke="#d8d8d4" stroke-width="1.2"><circle cx="8" cy="8" r="6.5"/><path d="M5.5 5c0 3 2.5 5.5 5 5.5l.8-1.2-1.5-.8-.7.7c-1-.4-1.9-1.3-2.3-2.3l.7-.7-.8-1.5z"/></svg>
        555-318-7094
      </li>
      <li>
        <svg viewBox="0 0 16 16" fill="none" stroke="#d8d8d4" stroke-width="1.2"><rect x="4.5" y="1.5" width="7" height="13" rx="1.2"/><line x1="7" y1="12.3" x2="9" y2="12.3"/></svg>
        555-642-1586
      </li>
      <li>
        <svg viewBox="0 0 16 16" fill="none" stroke="#d8d8d4" stroke-width="1.2"><rect x="1.5" y="3.5" width="13" height="9"/><path d="M1.5 3.5 8 9l6.5-5.5"/></svg>
        Tobias@briskel-example.ca
      </li>
      <li>
        <svg viewBox="0 0 16 16" fill="none" stroke="#d8d8d4" stroke-width="1.2"><circle cx="8" cy="8" r="6.5"/><ellipse cx="8" cy="8" rx="2.8" ry="6.5"/><line x1="1.5" y1="8" x2="14.5" y2="8"/></svg>
        <span>www.<span class="accent">briskel</span>.ca</span>
      </li>
    </ul>
  </section>
</main>
</body>
</html>
```